Whimsical business cards and stationary for accessories and gifts company
Please use your design expertise!
Whimsical business cards and stationary for accessories and gifts company - Children
Creative Brief
Bright & Fun-filled
Marisa J Tavelmor
Designer
Larkfield, New Harbor
LulaandPipDesigns@brightpost.net
www.LulaAndPipDesigns.craftnook.net www.friendwall.net/LulaandPipDesigns @LulaAndPipDesigns
Hair Accessories Party Favors Unique Gifts
Concepts
Business Cards for kids golf
Xpert Xpert
Kindly upload the Ai file of your logo.

```html
<!DOCTYPE html>
<html lang="en">
<head>
<meta charset="utf-8">
<title>Lula &amp; Pip – Business Cards</title>
<link href="https://fonts.googleapis.com/css2?family=Open+Sans:wght@400;600&display=swap" rel="stylesheet">
<style>
  :root {
    --bg: #e9e7ea;
    --card: #ffffff;
    --plum: #8e2a8b;
    --plum-soft: #c79ac6;
    --lilac: #e4cbe3;
    --ink: #5b5b5f;
    --rule: #b8b8bc;
  }
  * { margin: 0; padding: 0; box-sizing: border-box; }
  html, body { width: 1200px; height: 904px; overflow: hidden; }
  body {
    background: var(--bg);
    font-family: "Open Sans", Arial, sans-serif;
    color: var(--ink);
    display: flex;
    flex-direction: column;
    align-items: center;
    justify-content: center;
    gap: 40px;
  }
  .card {
    position: relative;
    width: 700px;
    height: 400px;
    background: var(--card);
    box-shadow: 0 6px 18px rgba(0,0,0,.12);
    overflow: hidden;
  }
  .card__decor {
    position: absolute;
    right: 0;
    top: 0;
    width: 300px;
    height: 400px;
  }
  .back__services {
    position: absolute;
    left: 44px;
    bottom: 40px;
    font-size: 15px;
    letter-spacing: .3px;
    display: flex;
    gap: 14px;
  }
  .back__services .sep { color: var(--rule); }

  .front__brand {
    position: absolute;
    left: 44px;
    top: 70px;
    width: 300px;
    text-align: center;
  }
  .brand-name {
    display: inline-flex;
    align-items: center;
    gap: 10px;
    font-size: 36px;
    font-weight: 600;
    color: var(--plum);
    line-height: 1;
  }
  .brand-dot {
    width: 22px; height: 22px;
    border-radius: 50%;
    background: var(--plum);
  }
  .brand-tagline {
    margin-top: 6px;
    font-size: 12px;
    letter-spacing: 2px;
    color: var(--plum-soft);
    text-transform: lowercase;
  }
  .front__contact {
    position: absolute;
    left: 44px;
    top: 200px;
    font-size: 13px;
    line-height: 1.45;
  }
  .person-name { font-size: 17px; font-weight: 600; color: var(--plum); }
  .person-role { margin-bottom: 10px; }
  .contact-line { display: flex; align-items: center; gap: 8px; white-space: nowrap; }
  .contact-icon {
    width: 11px; height: 11px;
    background: var(--ink);
    border-radius: 2px;
    flex: none;
  }
  .contact-line--plain { padding-left: 19px; }
</style>
</head>
<body>

  <section class="card card--back">
    <svg class="card__decor" viewBox="0 0 300 400" role="img" aria-label="Large decorative brand swirl motif in plum and lilac">
      <defs>
        <radialGradient id="decorBack" cx="70%" cy="45%" r="70%">
          <stop offset="0" stop-color="#d7b2d6"/>
          <stop offset="1" stop-color="#9a3d97"/>
        </radialGradient>
      </defs>
      <circle cx="250" cy="190" r="150" fill="url(#decorBack)" opacity=".55"/>
    </svg>
    <div class="back__services">
      <span>Hair Accessories</span><span class="sep">|</span>
      <span>Party Favors</span><span class="sep">|</span>
      <span>Unique Gifts</span>
    </div>
  </section>

  <section class="card card--front">
    <svg class="card__decor" viewBox="0 0 300 400" role="img" aria-label="Large decorative brand swirl motif in plum and lilac">
      <defs>
        <radialGradient id="decorFront" cx="70%" cy="45%" r="70%">
          <stop offset="0" stop-color="#d7b2d6"/>
          <stop offset="1" stop-color="#9a3d97"/>
        </radialGradient>
      </defs>
      <circle cx="260" cy="200" r="150" fill="url(#decorFront)" opacity=".55"/>
    </svg>

    <div class="front__brand">
      <div class="brand-name"><span class="brand-dot"></span>Lula &amp; Pip</div>
      <div class="brand-tagline">gift boutique</div>
    </div>

    <div class="front__contact">
      <div class="person-name">Marisa J Tavelmor</div>
      <div class="person-role">Designer</div>
      <div class="contact-line contact-line--plain">Larkfield, New Harbor</div>
      <div class="contact-line"><span class="contact-icon"></span>(555) 014-2287</div>
      <div class="contact-line"><span class="contact-icon"></span>LulaandPipDesigns@brightpost.net</div>
      <div class="contact-line"><span class="contact-icon"></span>www.LulaAndPipDesigns.craftnook.net</div>
      <div class="contact-line"><span class="contact-icon"></span>www.friendwall.net/LulaandPipDesigns</div>
      <div class="contact-line"><span class="contact-icon"></span>@LulaAndPipDesigns</div>
    </div>
  </section>

</body>
</html>
```